Audio/ Video Packaging Design for a Technology company.

We need a packaging design for a bag that is 7" wide and 10" high. The design will be for a new line of audio/video products. We would like to see designs that represent a superior quality product that provides a pure connection. We want the equivalent of a nice retail bag that you would find in a store like Tallow Mart. It should be a maximum of three colors. We really want something sharp, professional and eye catching, not whimsical or cartoonish. I've included a couple of examples below. I don't really like the designs of the bags, but I want you to see examples of what I'm looking for.

The company logo, which is uploaded, should be on the design. The words "audio and video products" should be either underneath the logo or to the side. Also, somewhere on the bag, we would like the words "For a Pure Connection"

The winner of this contest will likely get the opportunity for additional work as we have more products ready to launch.

Target Market(s)

resellers, consumers - men 25-60

Industry/Entity Type

It Company

Requirements
Must have
• It should be a maximum of three colors. We really want something sharp, professional and eye catching, not whimsical or cartoonish
Nice to have
• Eye-catching design. Utilize the entire bag but don't make it too busy.
Should not have
• Whimsical, cartoonish

```html
<!DOCTYPE html>
<html lang="en">
<head>
<meta charset="utf-8">
<title>Veltrion Cable Bag</title>
<link href="https://fonts.googleapis.com/css2?family=Montserrat:wght@400;500;600;700&display=swap" rel="stylesheet">
<style>
  :root {
    --stage: #d4d5d7;
    --bag-white: #ffffff;
    --ink-gray: #4a4b4d;
    --dark-gray: #58595b;
    --brand-blue: #3f80c6;
    --sky-blue: #5bc1ed;
    --hole: #545557;
    --window-light: #eceded;
    --window-mid: #c9cacb;
  }
  html, body {
    margin: 0;
    padding: 0;
    overflow: hidden;
  }
  .canvas {
    width: 1200px;
    height: 960px;
    background: var(--stage);
    position: relative;
    overflow: hidden;
    font-family: "Montserrat", sans-serif;
  }
  .bag {
    position: absolute;
    left: 303px;
    top: 40px;
    width: 594px;
    height: 880px;
    filter: drop-shadow(0 10px 18px rgba(0,0,0,0.18));
  }
  .brand-name { font-family: "Montserrat", sans-serif; font-weight: 500; fill: var(--ink-gray); }
  .brand-tagline { font-family: "Montserrat", sans-serif; font-weight: 500; fill: var(--brand-blue); }
  .product-title { font-family: "Montserrat", sans-serif; font-weight: 700; fill: var(--sky-blue); }
  .product-slogan { font-family: "Montserrat", sans-serif; font-weight: 500; fill: var(--bag-white); }
  .spec-label { font-family: "Montserrat", sans-serif; font-weight: 600; fill: var(--ink-gray); }
  .spec-detail { font-family: "Montserrat", sans-serif; font-weight: 400; fill: var(--sky-blue); }
  .origin-note { font-family: "Montserrat", sans-serif; font-weight: 500; fill: #7a7b7d; }
</style>
</head>
<body>
<div class="canvas">
  <svg class="bag" viewBox="0 0 602 891" xmlns="http://www.w3.org/2000/svg">
    <defs>
      <clipPath id="bag-outline">
        <rect x="0" y="0" width="602" height="891" rx="40" ry="40"/>
      </clipPath>
      <linearGradient id="window-fill" x1="0" y1="0" x2="1" y2="1">
        <stop offset="0" stop-color="var(--window-light)"/>
        <stop offset="0.5" stop-color="var(--window-mid)"/>
        <stop offset="1" stop-color="#9c9d9f"/>
      </linearGradient>
    </defs>

    <g clip-path="url(#bag-outline)">
      <!-- bag body -->
      <rect class="bag-body" x="0" y="0" width="602" height="891" fill="var(--bag-white)"/>

      <!-- hang hole -->
      <path class="hang-hole" d="M254 33 H286 C290 24 310 24 314 33 H348 A24 24 0 0 1 348 81 H254 A24 24 0 0 1 254 33 Z" fill="var(--hole)"/>

      <!-- seal line -->
      <line class="seal-line" x1="10" y1="118" x2="592" y2="118" stroke="#d6d6d6" stroke-width="1.5" stroke-dasharray="6 5"/>

      <!-- product window -->
      <path class="product-window" role="img" aria-label="Clear window showing the coiled black cable inside"
            d="M150 480 L575 178 Q602 170 602 200 L602 655 L350 633 Z" fill="url(#window-fill)"/>

      <!-- white cross over window -->
      <g class="window-cross" stroke="var(--bag-white)" stroke-width="40" stroke-linecap="butt">
        <line x1="270" y1="300" x2="650" y2="680"/>
        <line x1="330" y1="650" x2="640" y2="300"/>
      </g>

      <!-- lower colour blocks -->
      <polygon class="blue-block" points="0,433 278,625 90,891 0,891" fill="var(--brand-blue)"/>
      <rect class="circuit-field" role="img" aria-label="Faint circuit board trace pattern" x="0" y="560" width="200" height="270" fill="#4a88cb" opacity="0.5"/>
      <polygon class="sky-block" points="0,433 100,505 0,592" fill="var(--sky-blue)"/>
      <polygon class="gray-block" points="262,623 602,870 602,891 0,891 0,850" fill="var(--dark-gray)"/>
      <polygon class="white-band" points="262,623 350,633 602,800 602,870" fill="var(--bag-white)"/>
    </g>

    <!-- brand lockup -->
    <g class="brand-lockup" transform="translate(160 380) rotate(-35)">
      <rect class="brand-square" x="0" y="-44" width="40" height="40" fill="var(--brand-blue)"/>
      <text class="brand-name" x="54" y="-4" font-size="60" letter-spacing="2">VELTRION</text>
      <text class="brand-tagline" x="14" y="36" font-size="25" letter-spacing="1">audio and video products</text>
    </g>

    <!-- spec column -->
    <g class="spec-column">
      <rect x="42" y="730" width="32" height="110" fill="var(--bag-white)"/>
      <text class="spec-label" transform="translate(66 836) rotate(-90)" font-size="22" letter-spacing="2">HD-LINK</text>
      <text class="spec-detail" transform="translate(94 830) rotate(-90)" font-size="13">1.4 | 102 Gbps</text>
    </g>

    <!-- product title -->
    <text class="product-title" x="115" y="803" font-size="72" letter-spacing="1">CABLE</text>
    <text class="product-slogan" x="117" y="831" font-size="21">“For a Pure Connection”</text>

    <!-- origin note -->
    <text class="origin-note" transform="translate(590 836) rotate(-90)" font-size="10" letter-spacing="1" opacity="0.6">MADE IN CHINA</text>
  </svg>
</div>
</body>
</html>
```